Corvane Holdings , new business card design

investment firm with corporate clients . need double sided business card , vertical and horizontal options ,logo must be clear. prefer pantone colors only and sharp design. website also www.corvane.ae

Khalid Bin Tarrafi
Managing Director
Tel. +971 4 387 2940
Mobile +971 50 518 2403
khalid@corvane.ae
Q-Span Plaza, officw 18-B07, Warqa Gardens, Dubai

Contact Information for Business Card

Khalid Bin Tarrafi
Managing Director

Font styles to use
Serif

Colors

Designer to choose colors to be used in the design.

```html
<!DOCTYPE html>
<html lang="en">
<head>
<meta charset="utf-8">
<title>Corvane Holdings – Business Card</title>
<link rel="stylesheet" href="https://fonts.googleapis.com/css2?family=Open+Sans:wght@400;600;700&display=swap">
<style>
  :root {
    --canvas-bg: #d9dadc;
    --card-white: #ffffff;
    --card-shade: #eeeeef;
    --brand-blue: #4a6f9c;
    --brand-navy: #1f3c6e;
    --ink: #2e2e30;
    --ink-soft: #4a4a4d;
    --rule: #d4d4d6;
  }
  * { box-sizing: border-box; margin: 0; padding: 0; }
  html, body { width: 1200px; height: 900px; overflow: hidden; }
  body {
    background: var(--canvas-bg);
    font-family: "Open Sans", Arial, sans-serif;
    color: var(--ink);
    position: relative;
  }
  .card {
    position: absolute;
    width: 540px;
    height: 310px;
    border-radius: 18px;
    background: linear-gradient(160deg, var(--card-white) 40%, var(--card-shade) 100%);
    box-shadow: 0 10px 28px rgba(0,0,0,0.18);
    overflow: hidden;
  }
  .card--front { left: 80px; top: 90px; }
  .card--back { left: 580px; top: 500px; }

  /* wordmark */
  .wordmark {
    font-weight: 400;
    color: var(--ink);
    letter-spacing: 0.12em;
    text-transform: uppercase;
    display: flex;
    align-items: center;
    gap: 10px;
    white-space: nowrap;
  }
  .wordmark__square {
    width: 14px; height: 14px;
    background: var(--brand-blue);
    flex: none;
  }

  /* front */
  .front__logo {
    position: absolute;
    left: 34px; top: 118px;
    font-size: 19px;
  }
  .front__divider {
    position: absolute;
    left: 300px; top: 34px;
    width: 1px; height: 170px;
    background: var(--rule);
  }
  .front__details {
    position: absolute;
    left: 322px; top: 46px;
  }
  .person__name {
    font-size: 17px;
    font-weight: 700;
    color: var(--brand-blue);
  }
  .person__title {
    font-size: 12.5px;
    color: var(--ink-soft);
    margin-top: 1px;
  }
  .contact-list {
    list-style: none;
    margin-top: 12px;
    font-size: 13px;
    line-height: 19px;
    color: var(--ink);
  }
  .contact-list li { display: flex; align-items: center; gap: 8px; }
  .contact-list svg { width: 11px; height: 11px; fill: var(--brand-blue); flex: none; }

  .address-band {
    position: absolute;
    left: 0; right: 0; top: 214px;
    height: 38px;
    background: var(--brand-blue);
    border-top: 2px solid var(--brand-navy);
    border-bottom: 2px solid var(--brand-navy);
    display: flex;
    align-items: center;
    justify-content: center;
    color: #ffffff;
    font-size: 14px;
  }

  /* back */
  .back__logo {
    position: absolute;
    left: 0; right: 0; top: 112px;
    justify-content: center;
    font-size: 26px;
  }
  .back__web {
    position: absolute;
    left: 0; right: 0; top: 206px;
    text-align: center;
    font-size: 15px;
    letter-spacing: 0.22em;
    color: var(--ink);
  }
</style>
</head>
<body>

  <section class="card card--front" aria-label="Business card front">
    <div class="wordmark front__logo"><span class="wordmark__square"></span>Corvane Holdings</div>
    <div class="front__divider"></div>
    <div class="front__details">
      <div class="person__name">Khalid Bin Tarrafi</div>
      <div class="person__title">Managing Director</div>
      <ul class="contact-list">
        <li>
          <svg viewBox="0 0 24 24" aria-hidden="true"><path d="M6.6 10.8a15 15 0 0 0 6.6 6.6l2.2-2.2a1 1 0 0 1 1-.25 11.4 11.4 0 0 0 3.6.57 1 1 0 0 1 1 1V20a1 1 0 0 1-1 1A17 17 0 0 1 3 4a1 1 0 0 1 1-1h3.5a1 1 0 0 1 1 1c0 1.25.2 2.46.57 3.6a1 1 0 0 1-.25 1z"/></svg>
          +971 4 387 2940
        </li>
        <li>
          <svg viewBox="0 0 24 24" aria-hidden="true"><path d="M7 1h10a2 2 0 0 1 2 2v18a2 2 0 0 1-2 2H7a2 2 0 0 1-2-2V3a2 2 0 0 1 2-2zm0 3v14h10V4zm5 15.5a1 1 0 1 0 0 2 1 1 0 0 0 0-2z"/></svg>
          +971 50 518 2403
        </li>
        <li>
          <svg viewBox="0 0 24 24" aria-hidden="true"><path d="M2 5h20v14H2zm2 2v.5l8 5 8-5V7zm0 2.9V17h16V9.9l-8 5z"/></svg>
          khalid@corvane.ae
        </li>
      </ul>
    </div>
    <div class="address-band">Q-Span Plaza, officw 18-B07, Warqa Gardens, Dubai</div>
  </section>

  <section class="card card--back" aria-label="Business card back">
    <div class="wordmark back__logo"><span class="wordmark__square"></span>Corvane Holdings</div>
    <div class="back__web">www.corvane.ae</div>
  </section>

</body>
</html>
```